Stationery Design Project

We need a stationery design for our Norwegian trucking company. We have existed for about 15 years and our 12 drivers uses relatively new vehicles to transport goods around in northern Norway. Long distance routes with fresh fish og food transport is our main operations.

We have already made alogo that's printed on our trucks. The logo and a picture of our trucks is attached. I think the logo i crappy, but since its already in use, changing it is not an option in this round. Still using a better colour scheme in the overall stationery and more interesting fonts is possible (altso in the logo).

Company details:
Name: Kjelvraket AS
Organisation nr 873 615 309
Post adress: 8642 Raudvik

I like minimalism and simplicity. I am avalibly for questions in normal GMT working hours either here or on mail: ivar@fjordlast.no

Reason: Hi. Im extending the deadline because I needed some time to find a vector file of our logo. Sorry for the inconvenience

Hi, and thanks for all your interest in the project. Some updates:

-          I have decided to commit to using one of the designs. Some designer will get the payment.

-          I have extended the deadline with 24 hours since I needed some time to find our firms vector logo (a slow Swedish man was holding me up)

-          We will not choose a design before the deadline. No need to rush.

-          We have received a lot of great design and think there is a need to specified the product we want to make:

o   Business Card for all our employers. I just need the design and will duplicate with the correct numbers and name myself. The information on should be: Logo, employer’s name, Phone number, email, website, Postal number and address. Use this as a template: logo, Leif Brattvoll, 47382066, Leif@fjordlast.no,, fjordlast.no, 8642 Raudvik. The order and placement of the information is your creative decision.

o   Stickers to put on the goods we travel. On the sticker the should be the following information: Logo, phone number, Tekst and link: Fraktæ av Kjelvraket. Ke du syns? Fjordlast.no/tilbakemelding (this means: Handled by Kjelvraket. What do you think Fjordlast.no/feedback -à the link will be a feedback form). The placement the information and size is your creative decision with some stings: we have been thinking of using Drukko for printing and see that a size about 6x6 cm, 8x5 or something like that. (with 3000 copies our budget is 200 punds). Any suggestions of other suppliers are welcome. Drukko price calculator http://www.drukkolabelhouse.co.uk/digital-litho-printing/printing-labels-tags/stickers/

o   Letterhead with logo, address, phone number and organizational number.

o   Envelopes with logo,address, phone number and organizational number.

Have a nice day.

 

 

• Using the blue colour in the logo and using a similar graphic approch.

```html
<!DOCTYPE html>
<html lang="no">
<head>
<meta charset="utf-8">
<title>Kjelvraket – visittkort</title>
<link rel="stylesheet" href="https://fonts.googleapis.com/css2?family=PT+Sans:wght@400;700&display=swap">
<style>
  :root {
    --backdrop: #c9ccd1;
    --paper: #ffffff;
    --brand-deep: #0b4ea2;
    --brand-mid: #0a72b8;
    --brand-text: #0d5aa7;
    --ink: #2a2a2a;
    --rule-grey: #9a9a9a;
  }
  * { box-sizing: border-box; margin: 0; padding: 0; }
  html, body { width: 1200px; height: 751px; overflow: hidden; }
  body {
    background: var(--backdrop);
    font-family: "PT Sans", sans-serif;
    position: relative;
  }
  .card {
    position: absolute;
    width: 523px;
    height: 298px;
    border-radius: 16px;
    overflow: hidden;
  }
  .card--front { left: 65px; top: 52px; background: var(--paper); border: 1px solid #8a8a8a; }
  .card--back-deep { left: 621px; top: 52px; background: var(--brand-deep); }
  .card--back-white { left: 65px; top: 393px; background: var(--paper); border: 1px solid #8a8a8a; }
  .card--back-mid { left: 621px; top: 393px; background: var(--brand-mid); }

  .wordmark {
    position: absolute;
    left: 0; right: 0;
    display: flex;
    align-items: center;
    justify-content: center;
    gap: 14px;
    font-weight: 700;
    font-size: 50px;
    letter-spacing: 0.5px;
    color: var(--brand-text);
  }
  .wordmark__dot {
    width: 22px; height: 22px;
    border-radius: 50%;
    background: currentColor;
  }
  .wordmark--light { color: #ffffff; }

  .card--front .wordmark { top: 50px; }
  .card--back-deep .wordmark,
  .card--back-mid .wordmark,
  .card--back-white .wordmark { top: 128px; }

  .website {
    position: absolute;
    left: 0; right: 0;
    text-align: center;
    font-size: 17px;
    letter-spacing: 3.5px;
  }
  .card--front .website { top: 263px; color: var(--brand-text); }
  .card--back-deep .website,
  .card--back-mid .website { top: 248px; color: #ffffff; }
  .card--back-white .website { top: 249px; color: var(--ink); }

  .contact-name {
    position: absolute;
    right: 281px;
    top: 172px;
    text-align: right;
  }
  .contact-name__name {
    font-weight: 700;
    font-size: 20px;
    color: var(--brand-text);
    line-height: 24px;
  }
  .contact-name__address {
    font-size: 15px;
    color: var(--ink);
    margin-top: 3px;
    display: flex;
    justify-content: flex-end;
    align-items: center;
    gap: 5px;
  }
  .divider {
    position: absolute;
    left: 255px;
    top: 160px;
    width: 1px;
    height: 73px;
    background: var(--rule-grey);
  }
  .contact-list {
    position: absolute;
    left: 268px;
    top: 163px;
    list-style: none;
    font-size: 15px;
    color: var(--ink);
    line-height: 23px;
  }
  .contact-list li { display: flex; align-items: center; gap: 5px; }
  .contact-list .label { color: var(--brand-mid); }
  .icon { width: 11px; height: 11px; fill: var(--brand-text); }

  .base-rule {
    position: absolute;
    top: 245px;
    height: 3px;
    background: var(--brand-mid);
  }
  .base-rule--short { left: 0; width: 24px; }
  .base-rule--long { left: 30px; right: 0; }
</style>
</head>
<body>

  <section class="card card--front" aria-label="Visittkort forside">
    <div class="wordmark"><span class="wordmark__dot"></span>Kjelvraket</div>

    <div class="contact-name">
      <p class="contact-name__name">Leif Brattvoll</p>
      <p class="contact-name__address">
        <svg class="icon" viewBox="0 0 12 12" aria-hidden="true"><path d="M6 1 L11 5 V11 H1 V5 Z"/></svg>
        8642 Raudvik
      </p>
    </div>

    <div class="divider"></div>

    <ul class="contact-list">
      <li>
        <svg class="icon" viewBox="0 0 12 12" aria-hidden="true"><path d="M2.5 1 L4.5 1 L5.5 3.5 L4 4.6 Q5.2 7 7.4 8 L8.5 6.5 L11 7.5 L11 9.5 Q10.5 11 9 11 Q1 10 1 2.5 Q1 1 2.5 1 Z"/></svg>
        47382066
      </li>
      <li><span class="label">Org nr</span> 873 615 309</li>
      <li>
        <svg class="icon" viewBox="0 0 12 12" aria-hidden="true"><path d="M1 3 H11 V10 H1 Z M1 3 L6 7 L11 3" stroke="#fff" stroke-width="0.8"/></svg>
        Leif@fjordlast.no
      </li>
    </ul>

    <div class="base-rule base-rule--short"></div>
    <div class="base-rule base-rule--long"></div>

    <p class="website">www.fjordlast.no</p>
  </section>

  <section class="card card--back-deep" aria-label="Visittkort bakside, mørkeblå">
    <div class="wordmark wordmark--light"><span class="wordmark__dot"></span>Kjelvraket</div>
    <p class="website">www.fjordlast.no</p>
  </section>

  <section class="card card--back-white" aria-label="Visittkort bakside, hvit">
    <div class="wordmark"><span class="wordmark__dot"></span>Kjelvraket</div>
    <p class="website">www.fjordlast.no</p>
  </section>

  <section class="card card--back-mid" aria-label="Visittkort bakside, mellomblå">
    <div class="wordmark wordmark--light"><span class="wordmark__dot"></span>Kjelvraket</div>
    <p class="website">www.fjordlast.no</p>
  </section>

</body>
</html>
```